Moravel Aesthetic Doctor

I require an elegant, luxurious looking business card for my aesthetic business. I am a doctor and that will set me aside from competitors. I am planning to provide home and spa based treatments to clients with high expectations. I have attached my logo.

```html
<!DOCTYPE html>
<html lang="en">
<head>
<meta charset="utf-8">
<title>Moravel Aesthetic Doctor – Business Card</title>
<link rel="stylesheet" href="https://fonts.googleapis.com/css2?family=Cinzel:wght@400&family=Roboto:ital,wght@0,300;0,400;1,400&display=swap">
<style>
  :root {
    --stage: #e0e0de;
    --sky: #55b6ea;
    --ocean: #0b6fb8;
    --paper: #fafafa;
    --slate: #9aa2b1;
    --band: #a9aaab;
    --ink: #3f3f3f;
    --accent: #4fb0e6;
    --white: #ffffff;
  }
  * { margin: 0; padding: 0; box-sizing: border-box; }
  html, body { width: 1200px; height: 503px; overflow: hidden; }
  body { background: var(--stage); font-family: "Roboto", sans-serif; position: relative; }

  .card { position: absolute; top: 104px; width: 488px; height: 294px; overflow: hidden; }
  .card--front { left: 96px; background: linear-gradient(155deg, var(--sky) 0%, #2f8fd4 45%, var(--ocean) 100%); }
  .card--back { left: 614px; background: var(--paper); }

  .brand { position: absolute; font-family: "Cinzel", serif; font-weight: 400; line-height: 1; }
  .brand__mark { position: absolute; border-radius: 50%; border: 2px solid currentColor; }
  .brand__name, .brand__tag { position: absolute; white-space: nowrap; }

  .card--front .brand { color: var(--white); }
  .card--front .brand__mark { left: 48px; top: 46px; width: 104px; height: 104px; }
  .card--front .brand__name { left: 180px; top: 68px; font-size: 52px; letter-spacing: 1px; }
  .card--front .brand__tag { left: 184px; top: 124px; font-size: 21px; letter-spacing: 1px; }

  .services { position: absolute; left: 0; right: 0; top: 197px; text-align: center; color: var(--white); font-size: 13.5px; line-height: 18px; }
  .services .sep { margin: 0 8px; }
  .service-band { position: absolute; left: 0; right: 0; top: 246px; height: 24px; background: var(--band); color: var(--white); font-size: 12px; letter-spacing: 1.2px; text-align: center; line-height: 24px; }

  .swoosh { position: absolute; left: 0; top: 0; }
  .tagline { position: absolute; left: 28px; top: 22px; color: var(--white); font-size: 13.5px; font-weight: 300; line-height: 17px; }

  .card--back .brand { color: var(--accent); }
  .card--back .brand__mark { left: 191px; top: 86px; width: 80px; height: 80px; }
  .card--back .brand__name { right: 26px; top: 98px; font-size: 40px; letter-spacing: 1px; }
  .card--back .brand__tag { right: 26px; top: 140px; font-size: 17px; letter-spacing: 0.5px; }

  .contact { position: absolute; left: 28px; top: 183px; color: var(--ink); font-size: 13.5px; }
  .contact__follow { display: flex; align-items: center; gap: 5px; height: 18px; margin-bottom: 13px; }
  .social-dot { width: 12px; height: 12px; border-radius: 50%; background: var(--accent); display: inline-block; }
  .contact__row { display: flex; align-items: center; height: 18px; }
  .contact__row svg { width: 12px; height: 12px; margin-right: 9px; fill: var(--accent); }

  .doctor { position: absolute; right: 26px; top: 190px; text-align: right; }
  .doctor__name { font-size: 20px; font-weight: 300; color: var(--ink); line-height: 24px; }
  .doctor__post { font-size: 10px; font-style: italic; color: var(--accent); line-height: 14px; }
  .doctor__diploma { margin-top: 8px; font-size: 13.5px; color: var(--accent); line-height: 17px; }
</style>
</head>
<body>
  <section class="card card--front">
    <div class="brand">
      <span class="brand__mark"></span>
      <span class="brand__name">MORAVEL</span>
      <span class="brand__tag">AESTHETIC DOCTOR</span>
    </div>
    <p class="services">
      Dermal Injectables<span class="sep">|</span>Plasma Facials<span class="sep">|</span>Microneedling<br>
      Skin Boosters<span class="sep">|</span>Excessive Sweating
    </p>
    <div class="service-band">HOME AND SPA BASED TREATMENTS</div>
  </section>

  <section class="card card--back">
    <svg class="swoosh" width="488" height="294" viewBox="0 0 488 294" aria-hidden="true">
      <path d="M0,0 H488 V14 C420,10 340,28 260,52 C180,78 90,84 0,80 Z" fill="var(--sky)"/>
      <path d="M0,90 C90,94 180,86 260,62 C340,38 420,18 488,26 V38 C420,32 340,48 265,72 C185,98 90,106 0,104 Z" fill="var(--slate)"/>
      <path d="M250,28 C320,10 400,8 450,20 C400,16 320,20 262,34 Z" fill="var(--slate)"/>
    </svg>
    <p class="tagline">Home and Spa<br>Based Treatments</p>

    <div class="brand">
      <span class="brand__mark"></span>
      <span class="brand__name">MORAVEL</span>
      <span class="brand__tag">AESTHETIC DOCTOR</span>
    </div>

    <div class="contact">
      <div class="contact__follow">Follow us on: <span class="social-dot"></span><span class="social-dot"></span></div>
      <div class="contact__row">
        <svg viewBox="0 0 24 24"><path d="M6.6 10.8a15.1 15.1 0 0 0 6.6 6.6l2.2-2.2a1 1 0 0 1 1-.25 11.4 11.4 0 0 0 3.6.57 1 1 0 0 1 1 1V20a1 1 0 0 1-1 1A17 17 0 0 1 3 4a1 1 0 0 1 1-1h3.5a1 1 0 0 1 1 1c0 1.25.2 2.45.57 3.57a1 1 0 0 1-.25 1z"/></svg>
        0800 555 014
      </div>
      <div class="contact__row">
        <svg viewBox="0 0 24 24"><path d="M2 5h20v14H2z M2 5l10 8 10-8" fill="var(--accent)"/><path d="M3 6l9 7 9-7" fill="none" stroke="var(--paper)" stroke-width="1.5"/></svg>
        lena@moravel.co.nz
      </div>
      <div class="contact__row">
        <svg viewBox="0 0 24 24"><path d="M12 2a10 10 0 1 0 0 20 10 10 0 0 0 0-20zm0 2c.9 1.2 1.6 2.9 1.9 5h-3.8c.3-2.1 1-3.8 1.9-5zM4.3 11h3.8c.1-2 .5-3.8 1.1-5.2A8 8 0 0 0 4.3 11zm0 2a8 8 0 0 0 4.9 5.2c-.6-1.4-1-3.2-1.1-5.2zm5.8 0c.2 2.3.9 4.2 1.9 5.6 1-1.4 1.7-3.3 1.9-5.6zm5.8 0c-.1 2-.5 3.8-1.1 5.2a8 8 0 0 0 4.9-5.2zm3.8-2a8 8 0 0 0-4.9-5.2c.6 1.4 1 3.2 1.1 5.2z"/></svg>
        www.moravel.co.nz
      </div>
    </div>

    <div class="doctor">
      <p class="doctor__name">Dr Lena Varro</p>
      <p class="doctor__post">MRCPCH MD</p>
      <p class="doctor__diploma">Australasian Diploma of<br>Aesthetic Medicine</p>
    </div>
  </section>
</body>
</html>
```